Contemporary Business card for Event Manager

Needed for my startup events company in Melbourne. Events I manage will be based within the fashion industry, sporting events, product launches etc. Not weddings or small dinner parties. Therfore I am after something professional and aimed at high end corporate market; but with the added emphasis on not being too conservative or boring. I am happy with a pop of colour e.g. yellow or copper foil.

Target Market(s)

fashion industry, design industry, high end sporting events e.g. Polo, Grand Prix, corporate clients,

Industry/Entity Type

Fashion

Contact Information for Business Card

side 1
Lucy Brandt (can be upper or lower case, have a feature full stop between first and surname, or at the end of the nameetc) I am open to ideas. I would also be fine with my initials or name as a logo on the front (if this is the case my full name would need to go on the second side of the card.
2nd side:
Mobile: +61 400 817 263
email: lucy.brandt@mailnest.com.au

on one side of the card:
event management | brand activation | Advisory Services

Font styles to use
Serif
Sans Serif

Requirements
Must have
• side 2 must have
• mobile number
• email address
• event management | brand activation | Advisory Services
• ** my full name (Lucy Brandt) must be on the card somewhere)
Nice to have
• 1st side
• I see the card stock being either a dark grey, light grey, natural white or black (all matt colours on unprocessed card). I see the writing being copper foil, or foil white or foil black.
• To give you a feel for me, think: contemporary, minimalist, I love line drawings, concrete, white with grey vein marble, copper, white, grey, black...yes I do like colour....yellow (but pops of colour) ;) I would like the card to look designer but 'on trend' as I deal with a lot of design and fashion clients....styles - think the sophistication and simplicity of Vireaux or urban contemporary.
• some examples of what I like. Although please don't leet this limit you...I really am happy to have something a little more urban or design focused like a line drawing of an object, person too or a photo image too.
• https://www.moodtackle.com/pin/830165427719302846/
• https://www.moodtackle.com/pin/607281935540173268/
• https://www.moodtackle.com/pin/318746205913457092/
• https://www.moodtackle.com/pin/41983627530918476/
• https://www.moodtackle.com/pin/53128940672419087/
• https://www.moodtackle.com/pin/90316284750638152/
• https://www.moodtackle.com/pin/734092618450362918/
• https://www.moodtackle.com/pin/926354081736215407/
• https://www.moodtackle.com/pin/481627093518704356/
Should not have
• should not look commercial or have cartoonish looking logos. However happy with a simple line drawing or logo with initials etc.

```html
<!DOCTYPE html>
<html lang="en">
<head>
<meta charset="utf-8">
<title>Lucy Brandt — Business Card</title>
<link rel="stylesheet" href="https://fonts.googleapis.com/css2?family=Tinos:wght@400;700&display=swap">
<style>
  :root {
    --backdrop: #e7e4df;
    --card-black: #0b0b0b;
    --card-charcoal: #2f2f2f;
    --card-grey: #555555;
    --card-white: #f3f3f1;
    --accent-yellow: #e6dc12;
    --ink-dark: #1c1c1c;
    --ink-light: #ffffff;
  }
  * { margin: 0; padding: 0; box-sizing: border-box; }
  html, body {
    width: 1200px;
    height: 892px;
    overflow: hidden;
    background: var(--backdrop);
  }
  .canvas {
    width: 1200px;
    height: 892px;
    display: flex;
    flex-direction: column;
    align-items: center;
    justify-content: center;
    gap: 48px;
  }
  .card {
    width: 640px;
    height: 366px;
    display: block;
    box-shadow: 0 14px 30px rgba(0,0,0,0.28);
  }
  .card-name {
    font-family: "Tinos", "Times New Roman", serif;
    font-size: 40px;
    letter-spacing: 2px;
    fill: var(--ink-dark);
  }
  .card-phone {
    font-family: "Tinos", "Times New Roman", serif;
    font-size: 38px;
    fill: var(--ink-light);
  }
  .card-email {
    font-family: "Tinos", "Times New Roman", serif;
    font-size: 17px;
    fill: var(--ink-light);
  }
  .card-services {
    font-family: "Tinos", "Times New Roman", serif;
    font-size: 18px;
    fill: var(--ink-dark);
  }
</style>
</head>
<body>
<main class="canvas">

  <!-- Front: name side -->
  <svg class="card card-front" viewBox="0 0 640 366" xmlns="http://www.w3.org/2000/svg" aria-label="Business card front">
    <defs>
      <linearGradient id="charcoal-sheen" x1="0" y1="0" x2="0" y2="1">
        <stop offset="0" stop-color="#474747"/>
        <stop offset="1" stop-color="#2a2a2a"/>
      </linearGradient>
    </defs>
    <rect class="front-base" width="640" height="366" fill="url(#charcoal-sheen)"/>
    <polygon class="front-left-stripe" points="0,0 96,0 146,183 96,366 0,366" fill="var(--accent-yellow)"/>
    <polygon class="front-left-panel" points="0,0 80,0 130,183 80,366 0,366" fill="var(--card-black)"/>
    <polygon class="front-right-chevron" points="560,0 640,0 640,366 560,366 520,183" fill="var(--accent-yellow)"/>
    <rect class="front-name-band" x="136" y="136" width="390" height="94" fill="var(--card-white)"/>
    <text class="card-name" x="331" y="197" text-anchor="middle">LUCY BRANDT.</text>
  </svg>

  <!-- Back: contact side -->
  <svg class="card card-back" viewBox="0 0 640 366" xmlns="http://www.w3.org/2000/svg" aria-label="Business card back">
    <rect class="back-base" width="640" height="366" fill="var(--card-black)"/>
    <polygon class="back-left-wedge" points="0,40 70,183 0,326" fill="var(--accent-yellow)"/>
    <rect class="back-contact-band" x="0" y="120" width="640" height="126" fill="var(--card-grey)"/>
    <polygon class="back-edge-stripe" points="420,0 438,0 362,183 438,366 420,366 344,183" fill="var(--accent-yellow)"/>
    <polygon class="back-services-panel" points="446,0 640,0 640,366 446,366 372,183" fill="var(--card-white)"/>
    <polygon class="back-inner-stripe" points="470,26 478,26 414,183 478,340 470,340 404,183" fill="var(--accent-yellow)"/>

    <text class="card-phone" x="40" y="174">+61 400 817 263</text>
    <polygon class="back-pointer" points="300,190 322,190 311,208" fill="var(--accent-yellow)"/>
    <text class="card-email" x="40" y="224">lucy.brandt@mailnest.com.au</text>

    <text class="card-services" x="472" y="160">event management</text>
    <text class="card-services" x="472" y="186">brand activation</text>
    <text class="card-services" x="472" y="212">Advisory Services</text>
  </svg>

</main>
</body>
</html>
```